Moravel Aesthetic Doctor

I require an elegant, luxurious looking business card for my aesthetic business. I am a doctor and that will set me aside from competitors. I am planning to provide home and spa based treatments to clients with high expectations. I have attached my logo.

```html
<!DOCTYPE html>
<html lang="en">
<head>
<meta charset="utf-8">
<title>Moravel Aesthetic Doctor – Business Card</title>
<link rel="stylesheet" href="https://fonts.googleapis.com/css2?family=Lato:wght@400&family=Montserrat:wght@400;500&display=swap">
<style>
  :root {
    --bg: #dcdde1;
    --card: #fbfbfb;
    --blue: #2e8fd0;
    --blue-light: #9fd1ea;
    --blue-mid: #4aa6db;
    --text: #555a60;
    --text-dark: #4a4e53;
    --rule: #3a93d2;
  }
  * { box-sizing: border-box; margin: 0; padding: 0; }
  html, body { width: 1200px; height: 800px; overflow: hidden; }
  body {
    background: var(--bg);
    position: relative;
    font-family: "Montserrat", sans-serif;
    color: var(--text);
  }
  .card {
    position: absolute;
    left: 389px;
    width: 461px;
    height: 263px;
    background: var(--card);
  }
  .card--front { top: 93px; }
  .card--back { top: 422px; }

  .brand-artwork {
    position: absolute;
    left: 0;
    top: 23px;
    width: 252px;
    height: 226px;
    border-radius: 0 120px 90px 0;
    background: linear-gradient(120deg, var(--blue-light) 0%, var(--blue-mid) 55%, #2c79c0 100%);
    opacity: 0.85;
  }
  .wordmark {
    position: absolute;
    right: 26px;
    top: 190px;
    text-align: left;
    font-family: "Montserrat", sans-serif;
    font-weight: 400;
    color: var(--blue);
    line-height: 1.1;
  }
  .wordmark__name { display: block; font-size: 26px; letter-spacing: 3px; }
  .wordmark__tag { display: block; font-size: 11.5px; letter-spacing: 1.6px; margin-top: 4px; }

  .logo-lockup {
    position: absolute;
    left: 40px;
    top: 105px;
    display: flex;
    align-items: center;
    gap: 8px;
    font-weight: 400;
    color: var(--blue);
    line-height: 1.15;
  }
  .logo-lockup__dot {
    width: 44px; height: 44px;
    border-radius: 50%;
    background: var(--blue-light);
    flex: none;
  }
  .logo-lockup__name { display: block; font-size: 20px; letter-spacing: 2px; }
  .logo-lockup__tag { display: block; font-size: 9px; letter-spacing: 1.2px; margin-top: 2px; }

  .divider {
    position: absolute;
    left: 237px;
    top: 68px;
    width: 1px;
    height: 127px;
    background: var(--rule);
  }
  .details {
    position: absolute;
    left: 251px;
    top: 63px;
    width: 200px;
    font-size: 10.5px;
    line-height: 1.25;
  }
  .details__name { color: var(--blue); font-size: 12.5px; font-weight: 500; }
  .details__post { font-size: 7px; color: var(--text); font-weight: 400; letter-spacing: 0.2px; }
  .details__block { margin-top: 3px; }
  .details__block + .details__block { margin-top: 9px; }
  .contact { list-style: none; margin-top: 9px; }
  .contact li { display: flex; align-items: center; gap: 6px; height: 14px; }
  .contact svg { width: 8px; height: 8px; flex: none; fill: var(--blue); }
  .social { display: inline-flex; gap: 6px; margin-left: 14px; }
  .social span { width: 8px; height: 8px; border-radius: 50%; background: var(--blue); }

  .services {
    position: absolute;
    left: 0; right: 0;
    top: 231px;
    text-align: center;
    font-family: "Lato", sans-serif;
    font-size: 10.5px;
    color: var(--text-dark);
  }
</style>
</head>
<body>
  <section class="card card--front">
    <div class="brand-artwork" role="img" aria-label="Flowing blue brand artwork"></div>
    <div class="wordmark">
      <span class="wordmark__name">MORAVEL</span>
      <span class="wordmark__tag">AESTHETIC DOCTOR</span>
    </div>
  </section>

  <section class="card card--back">
    <div class="logo-lockup">
      <span class="logo-lockup__dot"></span>
      <div>
        <span class="logo-lockup__name">MORAVEL</span>
        <span class="logo-lockup__tag">AESTHETIC DOCTOR</span>
      </div>
    </div>
    <div class="divider"></div>
    <div class="details">
      <p class="details__name">Dr Elise Varnik <span class="details__post">MRCPCH MD</span></p>
      <p class="details__block">Australasian Diploma<br>of Aesthetic Medicine</p>
      <p class="details__block">Home and Spa<br>Based Treatments</p>
      <ul class="contact">
        <li><svg viewBox="0 0 10 10"><path d="M2 0.5l2 2-1 1.2c.6 1.3 1.6 2.3 2.9 2.9L7 5.5l2 2-1.3 1.8C4 9 1 6 .7 2z"/></svg>0800 555 014</li>
        <li><svg viewBox="0 0 10 10"><path d="M0 2h10v6H0z M0 2l5 3.5L10 2" stroke="#fff" stroke-width="0.8"/></svg>elise@moravel.co.nz</li>
        <li><svg viewBox="0 0 10 10"><circle cx="5" cy="5" r="4.5"/><path d="M.5 5h9M5 .5v9" stroke="#fff" stroke-width="0.6"/></svg>www.moravel.co.nz<span class="social"><span></span><span></span></span></li>
      </ul>
    </div>
    <p class="services">Dermal injectables - Plasma facials - Microneedling Skin boosters - Excessive sweating</p>
  </section>
</body>
</html>
```